Halberd Guard Services

Our Company is a security business which needs a cut edge design, the final product should have all relevant information and maintain a bold but modern and professional look.

Target Market(s)

A cut edge design which will attract any audience

Industry/Entity Type

Security

Contact Information for Business Card

HALBERD GUARD SERVICES

Gregor Lindqvist
Operations Manager
Phone: 0491 735 219

Email: info@halberdguard.com.au
Web: www.halberdguard.com.au

Requirements
Must have
• Must be double sided and contain all relevant information and the company logo.

```html
<!DOCTYPE html>
<html lang="en">
<head>
<meta charset="utf-8">
<title>Halberd Guard Services – Business Card</title>
<link rel="stylesheet" href="https://fonts.googleapis.com/css2?family=Michroma&display=swap">
<style>
  :root {
    --bg: #262626;
    --card-white: #ffffff;
    --slate: #546a72;
    --slate-dark: #3d5058;
    --orange: #f29a1f;
    --text-light: #ffffff;
  }
  * { margin: 0; padding: 0; box-sizing: border-box; }
  html, body { width: 1200px; height: 900px; overflow: hidden; }
  body {
    background: var(--bg);
    font-family: "Michroma", sans-serif;
    position: relative;
  }
  .card {
    position: absolute;
    width: 520px;
    height: 297px;
    background: var(--card-white);
    overflow: hidden;
    box-shadow: 0 10px 30px rgba(0,0,0,0.5);
  }
  .card--front { left: 110px; top: 110px; }
  .card--back { left: 570px; top: 470px; }

  .wordmark {
    display: flex;
    align-items: center;
    gap: 12px;
    color: var(--slate-dark);
    font-size: 19px;
    letter-spacing: 0.5px;
    white-space: nowrap;
  }
  .wordmark__dot {
    width: 26px; height: 26px;
    border-radius: 50%;
    background: var(--slate-dark);
    flex: none;
  }
  .card--front .wordmark {
    position: absolute;
    left: 0; right: 0; top: 134px;
    justify-content: center;
  }
  .card--back .wordmark {
    position: absolute;
    left: 26px; top: 52px;
    font-size: 18px;
  }

  .card__bands { position: absolute; inset: 0; }

  .holder {
    position: absolute;
    left: 26px; top: 210px;
  }
  .holder__name {
    color: var(--orange);
    font-size: 15px;
    letter-spacing: 0.3px;
  }
  .holder__role {
    color: var(--text-light);
    font-size: 9.5px;
    margin-top: 8px;
    letter-spacing: 0.4px;
  }

  .contacts {
    position: absolute;
    left: 258px; top: 178px;
    list-style: none;
  }
  .contacts li {
    display: flex;
    align-items: center;
    gap: 8px;
    color: var(--text-light);
    font-size: 9.5px;
    letter-spacing: 0.3px;
    margin-bottom: 9px;
  }
  .contacts svg { width: 12px; height: 12px; flex: none; }
</style>
</head>
<body>

  <section class="card card--front" aria-label="Card front">
    <div class="wordmark">
      <span class="wordmark__dot"></span>
      <span>HALBERD GUARD SERVICES</span>
    </div>
  </section>

  <section class="card card--back" aria-label="Card back">
    <svg class="card__bands" viewBox="0 0 520 297" width="520" height="297" aria-hidden="true">
      <polygon points="0,190 520,115 520,297 0,297" fill="var(--slate)"/>
      <polygon points="0,180 520,105 520,115 0,190" fill="var(--orange)"/>
      <polygon points="96,176 132,171 116,188" fill="var(--orange)"/>
    </svg>

    <div class="wordmark">
      <span class="wordmark__dot"></span>
      <span>HALBERD GUARD SERVICES</span>
    </div>

    <div class="holder">
      <p class="holder__name">GREGOR LINDQVIST</p>
      <p class="holder__role">OPERATIONS MANAGER</p>
    </div>

    <ul class="contacts">
      <li>
        <svg viewBox="0 0 12 12" aria-hidden="true"><rect x="1" y="1" width="10" height="10" rx="2" fill="var(--orange)"/><rect x="3" y="3" width="6" height="2" fill="var(--slate)"/><rect x="3" y="6.5" width="6" height="2.5" fill="var(--slate)"/></svg>
        <span>0491 735 219</span>
      </li>
      <li>
        <svg viewBox="0 0 12 12" aria-hidden="true"><rect x="0.5" y="2.5" width="11" height="7" fill="var(--orange)"/><polyline points="0.5,2.5 6,7 11.5,2.5" fill="none" stroke="var(--slate)" stroke-width="1"/></svg>
        <span>INFO@HALBERDGUARD.COM.AU</span>
      </li>
      <li>
        <svg viewBox="0 0 12 12" aria-hidden="true"><circle cx="6" cy="6" r="5.5" fill="var(--orange)"/><ellipse cx="6" cy="6" rx="2.2" ry="5.5" fill="none" stroke="var(--slate)" stroke-width="0.8"/><line x1="0.5" y1="6" x2="11.5" y2="6" stroke="var(--slate)" stroke-width="0.8"/></svg>
        <span>WWW.HALBERDGUARD.COM.AU</span>
      </li>
    </ul>
  </section>

</body>
</html>
```